DESKHAVEN COSPACE Website design and coding

DESKHAVEN COSPACE

DESKHAVEN is Galveston’s first (and currently only) shared business co-working space. We share the same upscale, casual work environment, but we work independently on our own (or our team’s) projects and goals. For only a flat $195 membership fee per month, you have your very own all-inclusive, fun, personal business office environment. Website is written (Word file #12, below); and all pictures etc provided. Galveston is a beachy, coastal, historic city an hour from Houston, Texas USA. Logo (file 11 below) is temporary only.

Target Market(s)

Outside sales people, medical students looking for study hall, Houston companies looking for local office, real estate agents, graphic artists, entrepreneurs, etc

Contact Information for Business Card

will discuss --want to combine with current business card with multiple businesses

Logo Text

DESKHAVEN COSPACE

Coding

Coded - Design and coding required

Number of Pages Required

5+ page

Colors
ec1f27
fbed22

Requirements
Nice to have
• maroon/wine dominant with yellow and red accents, gray base are the colors of the space--website could coordinate--but open to creative ideas/combinations

```html
<!DOCTYPE html>
<html lang="en">
<head>
<meta charset="utf-8">
<title>Deskhaven Cospace – Website Layouts</title>
<link href="https://fonts.googleapis.com/css2?family=Limelight&family=Montserrat:wght@400;600;700&display=swap" rel="stylesheet">
<style>
:root{
  --board:#e2e2e2;
  --black:#050505;
  --ink:#111;
  --charcoal:#2b2b2b;
  --graphite:#1b1b1b;
  --wine:#7d0b22;
  --wine-deep:#3b0913;
  --red:#ec1f27;
  --brick:#a01624;
  --yellow:#fbed22;
  --white:#fff;
  --muted:#c9c9c9;
  --social:#8a8a8a;
}
*{box-sizing:border-box;margin:0;padding:0}
html,body{width:892px;height:1200px;overflow:hidden;background:var(--board)}
body{position:relative;font-family:'Montserrat',sans-serif;color:var(--white)}
.page{position:absolute;top:23px;width:462px;height:2108px;transform:scale(.54);transform-origin:0 0;background:var(--black);overflow:hidden}
.page--a{left:48px}.page--b{left:330px}.page--c{left:611px}
section,header,footer{position:relative;width:462px}
.abs{position:absolute}
.deco{font-family:'Limelight',sans-serif;font-weight:400;letter-spacing:.5px}
.nav{height:40px;background:var(--black)}
.brand{left:18px;top:8px;width:80px;color:var(--red);font-weight:700;font-size:10px;line-height:11px;letter-spacing:.5px}
.menu{left:114px;top:16px;display:flex;gap:9px;font-size:5px;font-weight:600;text-transform:uppercase}
.menu .on{color:var(--yellow)}
.phone{left:392px;top:14px;font-size:6.5px;font-weight:600;display:flex;align-items:center;gap:3px}
.hero{height:260px}
.hero-photo{inset:0}
.photo-a{background:linear-gradient(160deg,#5a4a32 0%,#b08a4e 35%,#6b5634 60%,#2a2218 100%)}
.photo-b{background:linear-gradient(170deg,#8a8f96 0%,#c9c2b0 30%,#6c6a5c 55%,#b3862f 75%,#2d2a22 100%)}
.photo-c{background:linear-gradient(175deg,#1f2a36 0%,#5d6a78 35%,#2c3440 55%,#b78b2c 80%,#1a1a1a 100%)}
.arrow{top:100px;width:12px;height:22px;background:rgba(0,0,0,.7)}
.arrow--l{left:0}.arrow--r{right:0}
.hero-title{left:40px;right:40px;text-align:center;font-size:19px;line-height:22px;text-shadow:1px 1px 2px #000}
.tabs{left:33px;top:225px;width:396px;height:35px;display:flex}
.tab{flex:1;background:var(--black);text-align:center;padding-top:9px;font-size:6px;line-height:7px;color:var(--muted)}
.tab b{display:block;color:var(--white);font-weight:700}
.tab--offer{background:var(--brick);padding-top:4px;font-size:4.5px;line-height:5.5px}
.tab--offer b{font-size:7px;line-height:9px}
.about{height:236px;background:linear-gradient(180deg,#2e2e2e 0%,#0b0b0b 60%,#000 100%)}
.diamond{left:68px;top:45px;width:134px;height:134px;transform:rotate(45deg);border:2px solid var(--white);outline:1px solid #888;outline-offset:3px}
.section-h{font-size:11px;line-height:14px}
.about-h{left:247px;top:46px}
.about-p{left:247px;top:86px;width:195px;font-size:6.4px;line-height:11.5px;color:#d8d8d8}
.amenities{height:309px;background:linear-gradient(180deg,var(--wine) 0%,#5d0a1c 55%,var(--wine-deep) 100%)}
.center-h{left:0;right:0;text-align:center;font-size:12px}
.am-intro{left:60px;right:60px;top:52px;text-align:center;font-size:6px;line-height:11px}
.am-grid{left:46px;top:94px;width:376px;display:grid;grid-template-columns:repeat(4,1fr);row-gap:11px}
.am{display:flex;align-items:center;gap:5px;height:22px;padding-left:4px;border-right:1px solid rgba(255,255,255,.12);font-size:4.2px;line-height:5.5px;text-transform:uppercase}
.am:nth-child(4n){border-right:0}
.am svg{flex:none}
.btn-outline{left:200px;top:266px;width:64px;height:17px;border:1px solid var(--white);border-radius:9px;font-size:5px;font-weight:600;text-align:center;line-height:15px;letter-spacing:.4px}
.gallery{height:463px;background:var(--charcoal)}
.g{position:absolute}
.t1{background:linear-gradient(150deg,#6d7480,#c5bba3 45%,#a57a2e 80%)}
.t2{background:linear-gradient(140deg,#1c1c1c,#c7a21d 45%,#d8d2c2 70%,#2a2a2a)}
.t3{background:linear-gradient(170deg,#9aa2ab,#c09042 55%,#6b4d22)}
.t4{background:linear-gradient(165deg,#b9a88a,#7b6a4c 50%,#3e3427)}
.t5{background:linear-gradient(160deg,#d3cfc6,#8a8b8d 50%,#c6a25a)}
.t6{background:linear-gradient(170deg,#3b3b3d,#7b2a30 55%,#2a2a2a)}
.t7{background:linear-gradient(150deg,#e5d5b8,#b39461 50%,#8a9090)}
.t8{background:linear-gradient(150deg,#a8a39a,#c8c2ae 45%,#55504a)}
.t9{background:linear-gradient(160deg,#7a6a52,#a98746 50%,#3a3128)}
.t10{background:linear-gradient(150deg,#b01a32,#5b6b3a 40%,#6a5048 70%,#2c2626)}
.philosophy{height:243px;background:var(--black)}
.ph-frame{left:195px;top:64px;width:223px;height:144px;border:1px solid var(--red)}
.ph-photo{left:44px;top:76px;width:192px;height:122px}
.ph-h{left:254px;top:104px;width:158px;font-size:8.2px;font-weight:400;letter-spacing:.2px;white-space:nowrap}
.ph-p{left:254px;top:122px;width:152px;font-size:5.6px;line-height:9.3px;color:#cfcfcf}
.membership{height:212px;background:var(--graphite)}
.mb-photo{left:0;top:0;width:233px;height:212px}
.mb-h{left:260px;top:42px}
.price{left:257px;top:64px;width:131px;height:20px;border-radius:10px;background:var(--brick);font-size:10px;font-weight:600;line-height:20px;padding-left:12px}
.price em{font-style:normal;color:var(--yellow)}
.price small{font-size:4.5px;color:var(--yellow)}
.mb-p{left:262px;width:150px;font-size:4.6px;line-height:8.2px;color:#d6d6d6}
.free-day{left:260px;top:158px;width:150px;height:15px;border-radius:8px;background:var(--yellow);color:var(--ink);font-size:4.3px;font-weight:600;text-align:center;line-height:15px}
.free-day u{font-weight:700}
.contact{height:194px;background:linear-gradient(180deg,#8e101c 0%,#a2131f 50%,#6f0b15 100%)}
.rule{left:222px;top:51px;width:18px;height:1.5px;background:var(--yellow)}
.field{left:62px;width:174px;height:16px;border-radius:8px;background:var(--white);color:#666;font-size:4.6px;line-height:16px;padding-left:12px}
.textarea{left:241px;top:59px;width:171px;height:82px;border-radius:8px;background:var(--white);color:#666;font-size:4.6px;padding:8px 8px}
.send{left:204px;top:150px;width:70px;height:18px;border-radius:9px;background:var(--yellow);color:var(--ink);font-size:5px;font-weight:700;text-align:center;line-height:18px;letter-spacing:.4px}
.footer{height:151px;background:var(--ink)}
.fcol{top:29px;font-size:4.3px;line-height:9.6px;color:#cfcfcf}
.fcol h4{font-size:5.2px;font-weight:700;color:var(--white);margin-bottom:6px;letter-spacing:.2px}
.fline{display:flex;gap:5px;align-items:flex-start;line-height:8px;margin-bottom:4px}
.fline svg{flex:none;margin-top:1px}
.fline b{color:var(--white);font-weight:600}
.social{display:flex;align-items:center;gap:4px;margin-bottom:6px}
.dot{width:8px;height:8px;border-radius:50%;display:inline-block;background:var(--social)}
.copy{left:0;right:0;top:136px;text-align:center;font-size:3.6px;color:#8a8a8a}
</style>
</head>
<body>

<main class="page page--a">
  <header class="nav">
    <div class="abs brand">DESKHAVEN COSPACE</div>
    <nav class="abs menu"><span class="on">About</span><span>Amenities</span><span>Membership</span><span>Gallery</span><span>The Deskhaven Philosophy</span><span>Contact</span></nav>
    <div class="abs phone"><svg width="7" height="7" viewBox="0 0 10 10"><path d="M2 1l2 2-1 1.5c.8 1.5 1.8 2.5 3.3 3.3L7.8 6.8 9.8 8.8 8.6 10C4.5 9.6.4 5.5 0 1.4z" fill="#fbed22"/></svg>409-555-0148</div>
  </header>
  <section class="hero">
    <div class="abs hero-photo photo-a" role="img" aria-label="Photo of a warm-lit meeting room with a long wooden table and pendant lamps"></div>
    <div class="abs arrow arrow--l"></div><div class="abs arrow arrow--r"></div>
    <h1 class="abs hero-title deco" style="top:160px">WORK IT OUT WITH YOUR COWORKERS</h1>
    <div class="abs tabs">
      <div class="tab"><b>WORK OUTSIDE</b>THE HOME</div>
      <div class="tab tab--offer"><b>$195 MO.</b>ALL INCLUSIVE AND CLAIM<br>YOUR FREE DAY</div>
      <div class="tab"><b>WORK IT OUT WITH</b>YOUR COWORKERS</div>
      <div class="tab"><b>WORK OUT THE PATH</b>TO YOUR SUCCESS</div>
    </div>
  </section>
  <section class="about">
    <div class="abs diamond photo-b" role="img" aria-label="Photo of the lounge with leather sofas and lockers"></div>
    <h2 class="abs section-h deco about-h">ABOUT<br>DESKHAVEN COSPACE</h2>
    <p class="abs about-p">DESKHAVEN is Galveston’s first (and currently only) shared business co-working space. We share the same upscale, casual work environment, but we work independently on our own (or our team’s) projects and goals. For only a flat $195 membership fee per month, you have your very own all-inclusive, fun, personal business office environment.</p>
  </section>
  <section class="amenities">
    <h2 class="abs center-h deco" style="top:26px">AMENITIES</h2>
    <p class="abs am-intro">DESKHAVEN is the first Galveston co-working space, and offers all of the following features,<br>all included in your monthly $195 membership fee:</p>
    <div class="abs am-grid">
      <div class="am"><svg width="11" height="11" viewBox="0 0 11 11"><rect x="1" y="2" width="9" height="7" rx="1" fill="none" stroke="#fbed22"/></svg>Open office or a<br>private cubicle</div>
      <div class="am"><svg width="11" height="11" viewBox="0 0 11 11"><path d="M1 4a6 6 0 0 1 9 0M3 6a3.5 3.5 0 0 1 5 0" fill="none" stroke="#fbed22"/><circle cx="5.5" cy="8.5" r="1" fill="#fbed22"/></svg>Free WiFi</div>
      <div class="am"><svg width="11" height="11" viewBox="0 0 11 11"><rect x="1" y="2.5" width="9" height="6" fill="none" stroke="#fbed22"/><path d="M1 2.5l4.5 3.5 4.5-3.5" fill="none" stroke="#fbed22"/></svg>Mail service</div>
      <div class="am"><svg width="11" height="11" viewBox="0 0 11 11"><circle cx="5.5" cy="4" r="2" fill="none" stroke="#fbed22"/><path d="M1 10h9" stroke="#fbed22"/></svg>Private conference<br>rooms</div>
      <div class="am"><svg width="11" height="11" viewBox="0 0 11 11"><rect x="1" y="4" width="9" height="5" fill="none" stroke="#fbed22"/></svg>Communal coffee<br>bar and kitchen</div>
      <div class="am"><svg width="11" height="11" viewBox="0 0 11 11"><circle cx="3.5" cy="4" r="1.5" fill="none" stroke="#fbed22"/><circle cx="7.5" cy="4" r="1.5" fill="none" stroke="#fbed22"/><path d="M1 9.5a2.5 2.5 0 0 1 5 0M5 9.5a2.5 2.5 0 0 1 5 0" fill="none" stroke="#fbed22"/></svg>Great opportunity<br>for networking</div>
      <div class="am"><svg width="11" height="11" viewBox="0 0 11 11"><rect x="3" y="1" width="5" height="9" fill="none" stroke="#fbed22"/></svg>Building is a fabulous<br>example of mid-century<br>design</div>
      <div class="am"><svg width="11" height="11" viewBox="0 0 11 11"><circle cx="3.5" cy="4" r="1.5" fill="none" stroke="#fbed22"/><circle cx="7.5" cy="4" r="1.5" fill="none" stroke="#fbed22"/><path d="M1 9.5a2.5 2.5 0 0 1 5 0M5 9.5a2.5 2.5 0 0 1 5 0" fill="none" stroke="#fbed22"/></svg>Great opportunity<br>for networking</div>
      <div class="am"><svg width="11" height="11" viewBox="0 0 11 11"><circle cx="5.5" cy="5.5" r="4.5" fill="none" stroke="#fbed22"/><path d="M5.5 3v2.5H7.5" fill="none" stroke="#fbed22"/></svg>24 hour access</div>
      <div class="am"><svg width="11" height="11" viewBox="0 0 11 11"><path d="M1 3h9M2 3v7M9 3v7M1 7h9" fill="none" stroke="#fbed22"/></svg>Comfortable open<br>casual spaces</div>
      <div class="am"><svg width="11" height="11" viewBox="0 0 11 11"><path d="M3 2h5l-1 8H4z" fill="none" stroke="#fbed22"/></svg>Weekly free<br>happy hour</div>
      <div class="am"><svg width="11" height="11" viewBox="0 0 11 11"><rect x="1" y="1.5" width="9" height="6" fill="none" stroke="#fbed22"/><path d="M5.5 7.5v3" stroke="#fbed22"/></svg>Free conference/<br>presentation room</div>
      <div class="am"><svg width="11" height="11" viewBox="0 0 11 11"><circle cx="2.5" cy="3" r="1.3" fill="none" stroke="#fbed22"/><circle cx="8.5" cy="3" r="1.3" fill="none" stroke="#fbed22"/><path d="M2.5 5v5M8.5 5v5M4 7h3" fill="none" stroke="#fbed22"/></svg>Health and social<br>distance amenities</div>
      <div class="am"><svg width="11" height="11" viewBox="0 0 11 11"><rect x="1" y="4" width="9" height="4" fill="none" stroke="#fbed22"/><rect x="3" y="1" width="5" height="3" fill="none" stroke="#fbed22"/></svg>Use of copier/<br>printer</div>
      <div class="am"><svg width="11" height="11" viewBox="0 0 11 11"><rect x="1" y="1" width="9" height="9" fill="none" stroke="#fbed22"/><path d="M4 1v9M7 1v9" stroke="#fbed22"/></svg>Private lockable<br>lockers</div>
      <div class="am"><svg width="11" height="11" viewBox="0 0 11 11"><path d="M3 1h5v5H3zM5.5 6v4M3 10h5" fill="none" stroke="#fbed22"/></svg>Very comfortable<br>private office chairs</div>
      <div class="am"><svg width="11" height="11" viewBox="0 0 11 11"><rect x="1" y="1" width="9" height="9" fill="none" stroke="#fbed22"/><path d="M1 7l3-3 6 6" fill="none" stroke="#fbed22"/></svg>Great modern<br>interior design</div>
      <div class="am"><svg width="11" height="11" viewBox="0 0 11 11"><rect x="2.5" y="1" width="6" height="9" rx="1" fill="none" stroke="#fbed22"/><path d="M4 4h3" stroke="#fbed22"/></svg>Keyless, digital<br>door entry</div>
      <div class="am"><svg width="11" height="11" viewBox="0 0 11 11"><path d="M3 1v9M2 1v3h2V1M8 1c-1.5 1-1.5 4 0 4v5" fill="none" stroke="#fbed22"/></svg>Kitchen and<br>bar area</div>
      <div class="am"><svg width="11" height="11" viewBox="0 0 11 11"><rect x="1" y="1" width="9" height="9" rx="2" fill="none" stroke="#fbed22"/><circle cx="5.5" cy="5.5" r="2" fill="none" stroke="#fbed22"/></svg>Nightly hospital grade<br>ozone disinfection</div>
    </div>
    <div class="abs btn-outline">LEARN MORE</div>
  </section>
  <section class="gallery">
    <h2 class="abs center-h deco" style="top:22px">OUR GALLERY</h2>
    <div class="g t1" style="left:49px;top:55px;width:182px;height:86px" role="img" aria-label="Photo of the open workspace"></div>
    <div class="g t2" style="left:235px;top:55px;width:183px;height:86px" role="img" aria-label="Photo of black and yellow office chairs"></div>
    <div class="g t3" style="left:49px;top:148px;width:120px;height:90px" role="img" aria-label="Photo of wooden desks under pendant lamps"></div>
    <div class="g t4" style="left:173px;top:148px;width:121px;height:90px" role="img" aria-label="Photo of a glass-walled meeting room"></div>
    <div class="g t5" style="left:298px;top:148px;width:120px;height:90px" role="img" aria-label="Photo of the kitchen with steel appliances"></div>
    <div class="g t6" style="left:49px;top:244px;width:120px;height:90px" role="img" aria-label="Photo of the bar area with stools"></div>
    <div class="g t7" style="left:173px;top:244px;width:121px;height:90px" role="img" aria-label="Photo of the copier corner"></div>
    <div class="g t8" style="left:298px;top:244px;width:120px;height:90px" role="img" aria-label="Photo of the lounge sofas"></div>
    <div class="g t9" style="left:49px;top:342px;width:182px;height:86px" role="img" aria-label="Photo of the meeting room table"></div>
    <div class="g t10" style="left:235px;top:342px;width:183px;height:86px" role="img" aria-label="Photo of red lockers and a plant"></div>
  </section>
  <section class="philosophy">
    <h2 class="abs center-h deco" style="top:27px">THE DESKHAVEN PHILOSOPHY</h2>
    <div class="abs ph-frame"></div>
    <div class="abs ph-photo photo-b" role="img" aria-label="Photo of the lounge with a leather sofa and a yellow chair"></div>
    <h3 class="abs ph-h">DESKHAVEN THE COMPETITION</h3>
    <p class="abs ph-p">Because of the flexibility, prestigious location, opportunities to meet and network with active professionals, and the available tech and amenities, you have all the tools you need to excel in your chosen field.</p>
  </section>
  <section class="membership">
    <div class="abs mb-photo photo-c" role="img" aria-label="Photo of the workspace with pendant lamps and yellow chairs"></div>
    <h2 class="abs section-h deco mb-h">MEMBERSHIP</h2>
    <div class="abs price">For only <em>$195</em> <small>/monthly</small></div>
    <p class="abs mb-p" style="top:94px">Charged to your credit card, you get the all-inclusive amenities listed above, for one flat fee. The only “extras” are for copies, on a per-copy basis.</p>
    <p class="abs mb-p" style="top:125px">WiFi, coffee, use of the conference room, office use, use of the kitchen and all the other features listed under “AMENITIES” above, are INCLUDED at no additional cost</p>
    <div class="abs free-day">Get a FREE day, to try us out by emailing us at the <u>link here</u></div>
  </section>
  <section class="contact">
    <h2 class="abs center-h deco" style="top:30px">CONTACT US</h2>
    <div class="abs rule"></div>
    <div class="abs field" style="top:59px">Full Name*</div>
    <div class="abs field" style="top:80px">Email address*</div>
    <div class="abs field" style="top:101px">Phone Number*</div>
    <div class="abs field" style="top:122px">Description of your Business*</div>
    <div class="abs textarea">Write Message</div>
    <div class="abs send">SEND MESSAGE</div>
  </section>
  <footer class="footer">
    <div class="abs fcol" style="left:56px"><h4>NAVIGATION MENU</h4>About<br>Amenities<br>Membership<br>Gallery<br>The Deskhaven Philosophy<br>Contact</div>
    <div class="abs fcol" style="left:144px;width:105px"><h4>GET IN TOUCH</h4>
      <div class="fline"><svg width="8" height="8" viewBox="0 0 8 8"><circle cx="4" cy="4" r="4" fill="#fbed22"/><circle cx="4" cy="3.4" r="1.3" fill="#111"/></svg><span><b>Deskhaven Cospace</b><br>418 Seawall Row, Suite 12<br>Galveston, TX 77550</span></div>
      <div class="fline"><svg width="8" height="8" viewBox="0 0 8 8"><circle cx="4" cy="4" r="4" fill="#fbed22"/><rect x="2" y="2.7" width="4" height="2.6" fill="#111"/></svg><span>hello@deskhavencospace.com</span></div>
      <div class="fline"><svg width="8" height="8" viewBox="0 0 8 8"><circle cx="4" cy="4" r="4" fill="#fbed22"/><rect x="2.5" y="2" width="3" height="4" fill="#111"/></svg><span>409-555-0148</span></div>
    </div>
    <div class="abs fcol" style="left:256px;width:105px"><h4>MAILING ADDRESS</h4>
      <div class="fline"><svg width="8" height="8" viewBox="0 0 8 8"><circle cx="4" cy="4" r="4" fill="#fbed22"/><circle cx="4" cy="3.4" r="1.3" fill="#111"/></svg><span><b>Marlow Holdings</b><br>85 Bayou Lane, Suite 300<br>Houston, TX 77002</span></div>
      <div class="fline"><svg width="8" height="8" viewBox="0 0 8 8"><circle cx="4" cy="4" r="4" fill="#fbed22"/><rect x="2" y="2.7" width="4" height="2.6" fill="#111"/></svg><span>office@marlowholdings.com</span></div>
      <div class="fline"><svg width="8" height="8" viewBox="0 0 8 8"><circle cx="4" cy="4" r="4" fill="#fbed22"/><rect x="2.5" y="2" width="3" height="4" fill="#111"/></svg><span>409-555-0148</span></div>
    </div>
    <div class="abs fcol" style="left:366px"><h4>FOLLOW US</h4>
      <div class="social"><span class="dot"></span>Baylink</div>
      <div class="social"><span class="dot"></span>Workgrid</div>
      <div class="social"><span class="dot"></span>Snapcove</div>
    </div>
    <div class="abs copy">Copyright © 2020 Deskhaven Cospace &nbsp;|&nbsp; Privacy Policy</div>
  </footer>
</main>

<main class="page page--b">
  <header class="nav">
    <div class="abs brand">DESKHAVEN COSPACE</div>
    <nav class="abs menu"><span class="on">About</span><span>Amenities</span><span>Membership</span><span>Gallery</span><span>The Deskhaven Philosophy</span><span>Contact</span></nav>
    <div class="abs phone"><svg width="7" height="7" viewBox="0 0 10 10"><path d="M2 1l2 2-1 1.5c.8 1.5 1.8 2.5 3.3 3.3L7.8 6.8 9.8 8.8 8.6 10C4.5 9.6.4 5.5 0 1.4z" fill="#fbed22"/></svg>409-555-0148</div>
  </header>
  <section class="hero">
    <div class="abs hero-photo photo-b" role="img" aria-label="Photo of the open lounge with sofas, lockers and wooden desks"></div>
    <div class="abs arrow arrow--l"></div><div class="abs arrow arrow--r"></div>
    <h1 class="abs hero-title deco" style="top:160px">WORK OUT THE PATH<br>TO SUCCESS</h1>
    <div class="abs tabs">
      <div class="tab"><b>WORK OUTSIDE</b>THE HOME</div>
      <div class="tab tab--offer"><b>$195 MO.</b>ALL INCLUSIVE AND CLAIM<br>YOUR FREE DAY</div>
      <div class="tab"><b>WORK IT OUT WITH</b>YOUR COWORKERS</div>
      <div class="tab"><b>WORK OUT THE PATH</b>TO YOUR SUCCESS</div>
    </div>
  </section>
  <section class="about">
    <div class="abs diamond photo-b" role="img" aria-label="Photo of the lounge with leather sofas and lockers"></div>
    <h2 class="abs section-h deco about-h">ABOUT<br>DESKHAVEN COSPACE</h2>
    <p class="abs about-p">DESKHAVEN is Galveston’s first (and currently only) shared business co-working space. We share the same upscale, casual work environment, but we work independently on our own (or our team’s) projects and goals. For only a flat $195 membership fee per month, you have your very own all-inclusive, fun, personal business office environment.</p>
  </section>
  <section class="amenities">
    <h2 class="abs center-h deco" style="top:26px">AMENITIES</h2>
    <p class="abs am-intro">DESKHAVEN is the first Galveston co-working space, and offers all of the following features,<br>all included in your monthly $195 membership fee:</p>
    <div class="abs am-grid">
      <div class="am"><svg width="11" height="11" viewBox="0 0 11 11"><rect x="1" y="2" width="9" height="7" rx="1" fill="none" stroke="#fbed22"/></svg>Open office or a<br>private cubicle</div>
      <div class="am"><svg width="11" height="11" viewBox="0 0 11 11"><path d="M1 4a6 6 0 0 1 9 0M3 6a3.5 3.5 0 0 1 5 0" fill="none" stroke="#fbed22"/><circle cx="5.5" cy="8.5" r="1" fill="#fbed22"/></svg>Free WiFi</div>
      <div class="am"><svg width="11" height="11" viewBox="0 0 11 11"><rect x="1" y="2.5" width="9" height="6" fill="none" stroke="#fbed22"/><path d="M1 2.5l4.5 3.5 4.5-3.5" fill="none" stroke="#fbed22"/></svg>Mail service</div>
      <div class="am"><svg width="11" height="11" viewBox="0 0 11 11"><circle cx="5.5" cy="4" r="2" fill="none" stroke="#fbed22"/><path d="M1 10h9" stroke="#fbed22"/></svg>Private conference<br>rooms</div>
      <div class="am"><svg width="11" height="11" viewBox="0 0 11 11"><rect x="1" y="4" width="9" height="5" fill="none" stroke="#fbed22"/></svg>Communal coffee<br>bar and kitchen</div>
      <div class="am"><svg width="11" height="11" viewBox="0 0 11 11"><circle cx="3.5" cy="4" r="1.5" fill="none" stroke="#fbed22"/><circle cx="7.5" cy="4" r="1.5" fill="none" stroke="#fbed22"/><path d="M1 9.5a2.5 2.5 0 0 1 5 0M5 9.5a2.5 2.5 0 0 1 5 0" fill="none" stroke="#fbed22"/></svg>Great opportunity<br>for networking</div>
      <div class="am"><svg width="11" height="11" viewBox="0 0 11 11"><rect x="3" y="1" width="5" height="9" fill="none" stroke="#fbed22"/></svg>Building is a fabulous<br>example of mid-century<br>design</div>
      <div class="am"><svg width="11" height="11" viewBox="0 0 11 11"><circle cx="3.5" cy="4" r="1.5" fill="none" stroke="#fbed22"/><circle cx="7.5" cy="4" r="1.5" fill="none" stroke="#fbed22"/><path d="M1 9.5a2.5 2.5 0 0 1 5 0M5 9.5a2.5 2.5 0 0 1 5 0" fill="none" stroke="#fbed22"/></svg>Great opportunity<br>for networking</div>
      <div class="am"><svg width="11" height="11" viewBox="0 0 11 11"><circle cx="5.5" cy="5.5" r="4.5" fill="none" stroke="#fbed22"/><path d="M5.5 3v2.5H7.5" fill="none" stroke="#fbed22"/></svg>24 hour access</div>
      <div class="am"><svg width="11" height="11" viewBox="0 0 11 11"><path d="M1 3h9M2 3v7M9 3v7M1 7h9" fill="none" stroke="#fbed22"/></svg>Comfortable open<br>casual spaces</div>
      <div class="am"><svg width="11" height="11" viewBox="0 0 11 11"><path d="M3 2h5l-1 8H4z" fill="none" stroke="#fbed22"/></svg>Weekly free<br>happy hour</div>
      <div class="am"><svg width="11" height="11" viewBox="0 0 11 11"><rect x="1" y="1.5" width="9" height="6" fill="none" stroke="#fbed22"/><path d="M5.5 7.5v3" stroke="#fbed22"/></svg>Free conference/<br>presentation room</div>
      <div class="am"><svg width="11" height="11" viewBox="0 0 11 11"><circle cx="2.5" cy="3" r="1.3" fill="none" stroke="#fbed22"/><circle cx="8.5" cy="3" r="1.3" fill="none" stroke="#fbed22"/><path d="M2.5 5v5M8.5 5v5M4 7h3" fill="none" stroke="#fbed22"/></svg>Health and social<br>distance amenities</div>
      <div class="am"><svg width="11" height="11" viewBox="0 0 11 11"><rect x="1" y="4" width="9" height="4" fill="none" stroke="#fbed22"/><rect x="3" y="1" width="5" height="3" fill="none" stroke="#fbed22"/></svg>Use of copier/<br>printer</div>
      <div class="am"><svg width="11" height="11" viewBox="0 0 11 11"><rect x="1" y="1" width="9" height="9" fill="none" stroke="#fbed22"/><path d="M4 1v9M7 1v9" stroke="#fbed22"/></svg>Private lockable<br>lockers</div>
      <div class="am"><svg width="11" height="11" viewBox="0 0 11 11"><path d="M3 1h5v5H3zM5.5 6v4M3 10h5" fill="none" stroke="#fbed22"/></svg>Very comfortable<br>private office chairs</div>
      <div class="am"><svg width="11" height="11" viewBox="0 0 11 11"><rect x="1" y="1" width="9" height="9" fill="none" stroke="#fbed22"/><path d="M1 7l3-3 6 6" fill="none" stroke="#fbed22"/></svg>Great modern<br>interior design</div>
      <div class="am"><svg width="11" height="11" viewBox="0 0 11 11"><rect x="2.5" y="1" width="6" height="9" rx="1" fill="none" stroke="#fbed22"/><path d="M4 4h3" stroke="#fbed22"/></svg>Keyless, digital<br>door entry</div>
      <div class="am"><svg width="11" height="11" viewBox="0 0 11 11"><path d="M3 1v9M2 1v3h2V1M8 1c-1.5 1-1.5 4 0 4v5" fill="none" stroke="#fbed22"/></svg>Kitchen and<br>bar area</div>
      <div class="am"><svg width="11" height="11" viewBox="0 0 11 11"><rect x="1" y="1" width="9" height="9" rx="2" fill="none" stroke="#fbed22"/><circle cx="5.5" cy="5.5" r="2" fill="none" stroke="#fbed22"/></svg>Nightly hospital grade<br>ozone disinfection</div>
    </div>
    <div class="abs btn-outline">LEARN MORE</div>
  </section>
  <section class="gallery">
    <h2 class="abs center-h deco" style="top:22px">OUR GALLERY</h2>
    <div class="g t1" style="left:49px;top:55px;width:182px;height:86px" role="img" aria-label="Photo of the open workspace"></div>
    <div class="g t2" style="left:235px;top:55px;width:183px;height:86px" role="img" aria-label="Photo of black and yellow office chairs"></div>
    <div class="g t3" style="left:49px;top:148px;width:120px;height:90px" role="img" aria-label="Photo of wooden desks under pendant lamps"></div>
    <div class="g t4" style="left:173px;top:148px;width:121px;height:90px" role="img" aria-label="Photo of a glass-walled meeting room"></div>
    <div class="g t5" style="left:298px;top:148px;width:120px;height:90px" role="img" aria-label="Photo of the kitchen with steel appliances"></div>
    <div class="g t6" style="left:49px;top:244px;width:120px;height:90px" role="img" aria-label="Photo of the bar area with stools"></div>
    <div class="g t7" style="left:173px;top:244px;width:121px;height:90px" role="img" aria-label="Photo of the copier corner"></div>
    <div class="g t8" style="left:298px;top:244px;width:120px;height:90px" role="img" aria-label="Photo of the lounge sofas"></div>
    <div class="g t9" style="left:49px;top:342px;width:182px;height:86px" role="img" aria-label="Photo of the meeting room table"></div>
    <div class="g t10" style="left:235px;top:342px;width:183px;height:86px" role="img" aria-label="Photo of red lockers and a plant"></div>
  </section>
  <section class="philosophy">
    <h2 class="abs center-h deco" style="top:27px">THE DESKHAVEN PHILOSOPHY</h2>
    <div class="abs ph-frame"></div>
    <div class="abs ph-photo photo-b" role="img" aria-label="Photo of the lounge with a leather sofa and a yellow chair"></div>
    <h3 class="abs ph-h">DESKHAVEN THE COMPETITION</h3>
    <p class="abs ph-p">Because of the flexibility, prestigious location, opportunities to meet and network with active professionals, and the available tech and amenities, you have all the tools you need to excel in your chosen field.</p>
  </section>
  <section class="membership">
    <div class="abs mb-photo photo-c" role="img" aria-label="Photo of the workspace with pendant lamps and yellow chairs"></div>
    <h2 class="abs section-h deco mb-h">MEMBERSHIP</h2>
    <div class="abs price">For only <em>$195</em> <small>/monthly</small></div>
    <p class="abs mb-p" style="top:94px">Charged to your credit card, you get the all-inclusive amenities listed above, for one flat fee. The only “extras” are for copies, on a per-copy basis.</p>
    <p class="abs mb-p" style="top:125px">WiFi, coffee, use of the conference room, office use, use of the kitchen and all the other features listed under “AMENITIES” above, are INCLUDED at no additional cost</p>
    <div class="abs free-day">Get a FREE day, to try us out by emailing us at the <u>link here</u></div>
  </section>
  <section class="contact">
    <h2 class="abs center-h deco" style="top:30px">CONTACT US</h2>
    <div class="abs rule"></div>
    <div class="abs field" style="top:59px">Full Name*</div>
    <div class="abs field" style="top:80px">Email address*</div>
    <div class="abs field" style="top:101px">Phone Number*</div>
    <div class="abs field" style="top:122px">Description of your Business*</div>
    <div class="abs textarea">Write Message</div>
    <div class="abs send">SEND MESSAGE</div>
  </section>
  <footer class="footer">
    <div class="abs fcol" style="left:56px"><h4>NAVIGATION MENU</h4>About<br>Amenities<br>Membership<br>Gallery<br>The Deskhaven Philosophy<br>Contact</div>
    <div class="abs fcol" style="left:144px;width:105px"><h4>GET IN TOUCH</h4>
      <div class="fline"><svg width="8" height="8" viewBox="0 0 8 8"><circle cx="4" cy="4" r="4" fill="#fbed22"/><circle cx="4" cy="3.4" r="1.3" fill="#111"/></svg><span><b>Deskhaven Cospace</b><br>418 Seawall Row, Suite 12<br>Galveston, TX 77550</span></div>
      <div class="fline"><svg width="8" height="8" viewBox="0 0 8 8"><circle cx="4" cy="4" r="4" fill="#fbed22"/><rect x="2" y="2.7" width="4" height="2.6" fill="#111"/></svg><span>hello@deskhavencospace.com</span></div>
      <div class="fline"><svg width="8" height="8" viewBox="0 0 8 8"><circle cx="4" cy="4" r="4" fill="#fbed22"/><rect x="2.5" y="2" width="3" height="4" fill="#111"/></svg><span>409-555-0148</span></div>
    </div>
    <div class="abs fcol" style="left:256px;width:105px"><h4>MAILING ADDRESS</h4>
      <div class="fline"><svg width="8" height="8" viewBox="0 0 8 8"><circle cx="4" cy="4" r="4" fill="#fbed22"/><circle cx="4" cy="3.4" r="1.3" fill="#111"/></svg><span><b>Marlow Holdings</b><br>85 Bayou Lane, Suite 300<br>Houston, TX 77002</span></div>
      <div class="fline"><svg width="8" height="8" viewBox="0 0 8 8"><circle cx="4" cy="4" r="4" fill="#fbed22"/><rect x="2" y="2.7" width="4" height="2.6" fill="#111"/></svg><span>office@marlowholdings.com</span></div>
      <div class="fline"><svg width="8" height="8" viewBox="0 0 8 8"><circle cx="4" cy="4" r="4" fill="#fbed22"/><rect x="2.5" y="2" width="3" height="4" fill="#111"/></svg><span>409-555-0148</span></div>
    </div>
    <div class="abs fcol" style="left:366px"><h4>FOLLOW US</h4>
      <div class="social"><span class="dot"></span>Baylink</div>
      <div class="social"><span class="dot"></span>Workgrid</div>
      <div class="social"><span class="dot"></span>Snapcove</div>
    </div>
    <div class="abs copy">Copyright © 2020 Deskhaven Cospace &nbsp;|&nbsp; Privacy Policy</div>
  </footer>
</main>

<main class="page page--c">
  <header class="nav">
    <div class="abs brand">DESKHAVEN COSPACE</div>
    <nav class="abs menu"><span class="on">About</span><span>Amenities</span><span>Membership</span><span>Gallery</span><span>The Deskhaven Philosophy</span><span>Contact</span></nav>
    <div class="abs phone"><svg width="7" height="7" viewBox="0 0 10 10"><path d="M2 1l2 2-1 1.5c.8 1.5 1.8 2.5 3.3 3.3L7.8 6.8 9.8 8.8 8.6 10C4.5 9.6.4 5.5 0 1.4z" fill="#fbed22"/></svg>409-555-0148</div>
  </header>
  <section class="hero">
    <div class="abs hero-photo photo-c" role="img" aria-label="Photo of the workspace at dusk with pendant lamps and yellow chairs"></div>
    <div class="abs arrow arrow--l"></div><div class="abs arrow arrow--r"></div>
    <h1 class="abs hero-title deco" style="top:188px">WORK OUTSIDE THE HOME</h1>
    <div class="abs tabs">
      <div class="tab"><b>WORK OUTSIDE</b>THE HOME</div>
      <div class="tab tab--offer"><b>$195 MO.</b>ALL INCLUSIVE AND CLAIM<br>YOUR FREE DAY</div>
      <div class="tab"><b>WORK IT OUT WITH</b>YOUR COWORKERS</div>
      <div class="tab"><b>WORK OUT THE PATH</b>TO YOUR SUCCESS</div>
    </div>
  </section>
  <section class="about">
    <div class="abs diamond photo-b" role="img" aria-label="Photo of the lounge with leather sofas and lockers"></div>
    <h2 class="abs section-h deco about-h">ABOUT<br>DESKHAVEN COSPACE</h2>
    <p class="abs about-p">DESKHAVEN is Galveston’s first (and currently only) shared business co-working space. We share the same upscale, casual work environment, but we work independently on our own (or our team’s) projects and goals. For only a flat $195 membership fee per month, you have your very own all-inclusive, fun, personal business office environment.</p>
  </section>
  <section class="amenities">
    <h2 class="abs center-h deco" style="top:26px">AMENITIES</h2>
    <p class="abs am-intro">DESKHAVEN is the first Galveston co-working space, and offers all of the following features,<br>all included in your monthly $195 membership fee:</p>
    <div class="abs am-grid">
      <div class="am"><svg width="11" height="11" viewBox="0 0 11 11"><rect x="1" y="2" width="9" height="7" rx="1" fill="none" stroke="#fbed22"/></svg>Open office or a<br>private cubicle</div>
      <div class="am"><svg width="11" height="11" viewBox="0 0 11 11"><path d="M1 4a6 6 0 0 1 9 0M3 6a3.5 3.5 0 0 1 5 0" fill="none" stroke="#fbed22"/><circle cx="5.5" cy="8.5" r="1" fill="#fbed22"/></svg>Free WiFi</div>
      <div class="am"><svg width="11" height="11" viewBox="0 0 11 11"><rect x="1" y="2.5" width="9" height="6" fill="none" stroke="#fbed22"/><path d="M1 2.5l4.5 3.5 4.5-3.5" fill="none" stroke="#fbed22"/></svg>Mail service</div>
      <div class="am"><svg width="11" height="11" viewBox="0 0 11 11"><circle cx="5.5" cy="4" r="2" fill="none" stroke="#fbed22"/><path d="M1 10h9" stroke="#fbed22"/></svg>Private conference<br>rooms</div>
      <div class="am"><svg width="11" height="11" viewBox="0 0 11 11"><rect x="1" y="4" width="9" height="5" fill="none" stroke="#fbed22"/></svg>Communal coffee<br>bar and kitchen</div>
      <div class="am"><svg width="11" height="11" viewBox="0 0 11 11"><circle cx="3.5" cy="4" r="1.5" fill="none" stroke="#fbed22"/><circle cx="7.5" cy="4" r="1.5" fill="none" stroke="#fbed22"/><path d="M1 9.5a2.5 2.5 0 0 1 5 0M5 9.5a2.5 2.5 0 0 1 5 0" fill="none" stroke="#fbed22"/></svg>Great opportunity<br>for networking</div>
      <div class="am"><svg width="11" height="11" viewBox="0 0 11 11"><rect x="3" y="1" width="5" height="9" fill="none" stroke="#fbed22"/></svg>Building is a fabulous<br>example of mid-century<br>design</div>
      <div class="am"><svg width="11" height="11" viewBox="0 0 11 11"><circle cx="3.5" cy="4" r="1.5" fill="none" stroke="#fbed22"/><circle cx="7.5" cy="4" r="1.5" fill="none" stroke="#fbed22"/><path d="M1 9.5a2.5 2.5 0 0 1 5 0M5 9.5a2.5 2.5 0 0 1 5 0" fill="none" stroke="#fbed22"/></svg>Great opportunity<br>for networking</div>
      <div class="am"><svg width="11" height="11" viewBox="0 0 11 11"><circle cx="5.5" cy="5.5" r="4.5" fill="none" stroke="#fbed22"/><path d="M5.5 3v2.5H7.5" fill="none" stroke="#fbed22"/></svg>24 hour access</div>
      <div class="am"><svg width="11" height="11" viewBox="0 0 11 11"><path d="M1 3h9M2 3v7M9 3v7M1 7h9" fill="none" stroke="#fbed22"/></svg>Comfortable open<br>casual spaces</div>
      <div class="am"><svg width="11" height="11" viewBox="0 0 11 11"><path d="M3 2h5l-1 8H4z" fill="none" stroke="#fbed22"/></svg>Weekly free<br>happy hour</div>
      <div class="am"><svg width="11" height="11" viewBox="0 0 11 11"><rect x="1" y="1.5" width="9" height="6" fill="none" stroke="#fbed22"/><path d="M5.5 7.5v3" stroke="#fbed22"/></svg>Free conference/<br>presentation room</div>
      <div class="am"><svg width="11" height="11" viewBox="0 0 11 11"><circle cx="2.5" cy="3" r="1.3" fill="none" stroke="#fbed22"/><circle cx="8.5" cy="3" r="1.3" fill="none" stroke="#fbed22"/><path d="M2.5 5v5M8.5 5v5M4 7h3" fill="none" stroke="#fbed22"/></svg>Health and social<br>distance amenities</div>
      <div class="am"><svg width="11" height="11" viewBox="0 0 11 11"><rect x="1" y="4" width="9" height="4" fill="none" stroke="#fbed22"/><rect x="3" y="1" width="5" height="3" fill="none" stroke="#fbed22"/></svg>Use of copier/<br>printer</div>
      <div class="am"><svg width="11" height="11" viewBox="0 0 11 11"><rect x="1" y="1" width="9" height="9" fill="none" stroke="#fbed22"/><path d="M4 1v9M7 1v9" stroke="#fbed22"/></svg>Private lockable<br>lockers</div>
      <div class="am"><svg width="11" height="11" viewBox="0 0 11 11"><path d="M3 1h5v5H3zM5.5 6v4M3 10h5" fill="none" stroke="#fbed22"/></svg>Very comfortable<br>private office chairs</div>
      <div class="am"><svg width="11" height="11" viewBox="0 0 11 11"><rect x="1" y="1" width="9" height="9" fill="none" stroke="#fbed22"/><path d="M1 7l3-3 6 6" fill="none" stroke="#fbed22"/></svg>Great modern<br>interior design</div>
      <div class="am"><svg width="11" height="11" viewBox="0 0 11 11"><rect x="2.5" y="1" width="6" height="9" rx="1" fill="none" stroke="#fbed22"/><path d="M4 4h3" stroke="#fbed22"/></svg>Keyless, digital<br>door entry</div>
      <div class="am"><svg width="11" height="11" viewBox="0 0 11 11"><path d="M3 1v9M2 1v3h2V1M8 1c-1.5 1-1.5 4 0 4v5" fill="none" stroke="#fbed22"/></svg>Kitchen and<br>bar area</div>
      <div class="am"><svg width="11" height="11" viewBox="0 0 11 11"><rect x="1" y="1" width="9" height="9" rx="2" fill="none" stroke="#fbed22"/><circle cx="5.5" cy="5.5" r="2" fill="none" stroke="#fbed22"/></svg>Nightly hospital grade<br>ozone disinfection</div>
    </div>
    <div class="abs btn-outline">LEARN MORE</div>
  </section>
  <section class="gallery">
    <h2 class="abs center-h deco" style="top:22px">OUR GALLERY</h2>
    <div class="g t1" style="left:49px;top:55px;width:182px;height:86px" role="img" aria-label="Photo of the open workspace"></div>
    <div class="g t2" style="left:235px;top:55px;width:183px;height:86px" role="img" aria-label="Photo of black and yellow office chairs"></div>
    <div class="g t3" style="left:49px;top:148px;width:120px;height:90px" role="img" aria-label="Photo of wooden desks under pendant lamps"></div>
    <div class="g t4" style="left:173px;top:148px;width:121px;height:90px" role="img" aria-label="Photo of a glass-walled meeting room"></div>
    <div class="g t5" style="left:298px;top:148px;width:120px;height:90px" role="img" aria-label="Photo of the kitchen with steel appliances"></div>
    <div class="g t6" style="left:49px;top:244px;width:120px;height:90px" role="img" aria-label="Photo of the bar area with stools"></div>
    <div class="g t7" style="left:173px;top:244px;width:121px;height:90px" role="img" aria-label="Photo of the copier corner"></div>
    <div class="g t8" style="left:298px;top:244px;width:120px;height:90px" role="img" aria-label="Photo of the lounge sofas"></div>
    <div class="g t9" style="left:49px;top:342px;width:182px;height:86px" role="img" aria-label="Photo of the meeting room table"></div>
    <div class="g t10" style="left:235px;top:342px;width:183px;height:86px" role="img" aria-label="Photo of red lockers and a plant"></div>
  </section>
  <section class="philosophy">
    <h2 class="abs center-h deco" style="top:27px">THE DESKHAVEN PHILOSOPHY</h2>
    <div class="abs ph-frame"></div>
    <div class="abs ph-photo photo-b" role="img" aria-label="Photo of the lounge with a leather sofa and a yellow chair"></div>
    <h3 class="abs ph-h">DESKHAVEN THE COMPETITION</h3>
    <p class="abs ph-p">Because of the flexibility, prestigious location, opportunities to meet and network with active professionals, and the available tech and amenities, you have all the tools you need to excel in your chosen field.</p>
  </section>
  <section class="membership">
    <div class="abs mb-photo photo-c" role="img" aria-label="Photo of the workspace with pendant lamps and yellow chairs"></div>
    <h2 class="abs section-h deco mb-h">MEMBERSHIP</h2>
    <div class="abs price">For only <em>$195</em> <small>/monthly</small></div>
    <p class="abs mb-p" style="top:94px">Charged to your credit card, you get the all-inclusive amenities listed above, for one flat fee. The only “extras” are for copies, on a per-copy basis.</p>
    <p class="abs mb-p" style="top:125px">WiFi, coffee, use of the conference room, office use, use of the kitchen and all the other features listed under “AMENITIES” above, are INCLUDED at no additional cost</p>
    <div class="abs free-day">Get a FREE day, to try us out by emailing us at the <u>link here</u></div>
  </section>
  <section class="contact">
    <h2 class="abs center-h deco" style="top:30px">CONTACT US</h2>
    <div class="abs rule"></div>
    <div class="abs field" style="top:59px">Full Name*</div>
    <div class="abs field" style="top:80px">Email address*</div>
    <div class="abs field" style="top:101px">Phone Number*</div>
    <div class="abs field" style="top:122px">Description of your Business*</div>
    <div class="abs textarea">Write Message</div>
    <div class="abs send">SEND MESSAGE</div>
  </section>
  <footer class="footer">
    <div class="abs fcol" style="left:56px"><h4>NAVIGATION MENU</h4>About<br>Amenities<br>Membership<br>Gallery<br>The Deskhaven Philosophy<br>Contact</div>
    <div class="abs fcol" style="left:144px;width:105px"><h4>GET IN TOUCH</h4>
      <div class="fline"><svg width="8" height="8" viewBox="0 0 8 8"><circle cx="4" cy="4" r="4" fill="#fbed22"/><circle cx="4" cy="3.4" r="1.3" fill="#111"/></svg><span><b>Deskhaven Cospace</b><br>418 Seawall Row, Suite 12<br>Galveston, TX 77550</span></div>
      <div class="fline"><svg width="8" height="8" viewBox="0 0 8 8"><circle cx="4" cy="4" r="4" fill="#fbed22"/><rect x="2" y="2.7" width="4" height="2.6" fill="#111"/></svg><span>hello@deskhavencospace.com</span></div>
      <div class="fline"><svg width="8" height="8" viewBox="0 0 8 8"><circle cx="4" cy="4" r="4" fill="#fbed22"/><rect x="2.5" y="2" width="3" height="4" fill="#111"/></svg><span>409-555-0148</span></div>
    </div>
    <div class="abs fcol" style="left:256px;width:105px"><h4>MAILING ADDRESS</h4>
      <div class="fline"><svg width="8" height="8" viewBox="0 0 8 8"><circle cx="4" cy="4" r="4" fill="#fbed22"/><circle cx="4" cy="3.4" r="1.3" fill="#111"/></svg><span><b>Marlow Holdings</b><br>85 Bayou Lane, Suite 300<br>Houston, TX 77002</span></div>
      <div class="fline"><svg width="8" height="8" viewBox="0 0 8 8"><circle cx="4" cy="4" r="4" fill="#fbed22"/><rect x="2" y="2.7" width="4" height="2.6" fill="#111"/></svg><span>office@marlowholdings.com</span></div>
      <div class="fline"><svg width="8" height="8" viewBox="0 0 8 8"><circle cx="4" cy="4" r="4" fill="#fbed22"/><rect x="2.5" y="2" width="3" height="4" fill="#111"/></svg><span>409-555-0148</span></div>
    </div>
    <div class="abs fcol" style="left:366px"><h4>FOLLOW US</h4>
      <div class="social"><span class="dot"></span>Baylink</div>
      <div class="social"><span class="dot"></span>Workgrid</div>
      <div class="social"><span class="dot"></span>Snapcove</div>
    </div>
    <div class="abs copy">Copyright © 2020 Deskhaven Cospace &nbsp;|&nbsp; Privacy Policy</div>
  </footer>
</main>

</body>
</html>
```